New Business Card Design for Manufacturing

We are an engineering/manufacturing company that offers Advanced machining/assembly/engineering services, as well as innovative products for the heavy duty engine cooling markets.

We are looking to get a new business card designed that is clean and modern looking, but still fits the wide range of technical/skilled work we do.

- We hope to use this design as the base for other design work in new Presentations, web, and print work.

Industry/Entity Type

Engineering

Contact Information for Business Card

Our preferred color of blue is (RGB) 22/71/159 but can vary slightly from that color. Our content will be our Logo and full company name (Vantrell Forge Works, Inc.), company address, name, job title, phone number with extension, cell number, fax number, website, and email address on the cards.
We'd like the full company name next to the logo, but we are open to other interpretations of that layout.
Preferably, we would like the back side to be clean with just our logo, and the front to contain all of the contact information.

Colors
2f74b4
0355a3
85abd2

Requirements
Must have
• - Logo, company name, needed content - We are open to interpretation beyond that.
• - Standard size business card.
• - Horizontal orientation.
• - Enough space for lengthy names / job titles (for example, a job title could read "Directory of Human Resources" or "V.P. of Governmental Affairs"). We need this to look clean, whether the title be short (CEO) or long (as described above).

```html
<!DOCTYPE html>
<html lang="en">
<head>
<meta charset="utf-8">
<title>Vantrell Forge Works – Business Card</title>
<link rel="stylesheet" href="https://fonts.googleapis.com/css2?family=Arimo:wght@400;700&display=swap">
<style>
  :root {
    --backdrop: #4a423c;
    --card: #121212;
    --card-edge: #1d1d1d;
    --brand-blue: #2f74b4;
    --text-light: #e9e9e9;
    --text-muted: #9a9a9a;
    --silver: #d6d6d6;
    --divider: #5a5a5a;
  }
  * { margin: 0; padding: 0; box-sizing: border-box; }
  html, body {
    width: 1200px; height: 900px; overflow: hidden;
    background: var(--backdrop);
    font-family: "Arimo", Arial, sans-serif;
  }
  .canvas { position: relative; width: 1200px; height: 900px; }

  .card {
    position: absolute; top: 295px;
    width: 540px; height: 310px;
    background: var(--card);
    border: 1px solid var(--card-edge);
    border-radius: 3px;
  }
  .card--front { left: 40px; }
  .card--back { left: 620px; }

  /* Front side */
  .front-brand {
    position: absolute; left: 0; top: 0; width: 262px; height: 100%;
    display: flex; align-items: center; justify-content: center; gap: 10px;
  }
  .brand-mark { width: 16px; height: 16px; background: var(--brand-blue); }
  .brand-name--front {
    font-weight: 700; font-size: 34px; letter-spacing: 1px;
    color: var(--brand-blue);
  }
  .front-divider {
    position: absolute; left: 262px; top: 58px; width: 1px; height: 194px;
    background: var(--divider);
  }
  .contact {
    position: absolute; left: 286px; top: 58px; right: 20px;
    color: var(--text-light); font-size: 15px; line-height: 1.25;
  }
  .contact-name {
    color: var(--brand-blue); font-size: 19px; font-weight: 400;
    letter-spacing: 0.5px; text-transform: uppercase;
  }
  .contact-title { font-size: 14px; margin-bottom: 10px; }
  .contact-list { list-style: none; }
  .contact-list li { display: flex; align-items: center; gap: 8px; }
  .contact-list svg { width: 10px; height: 10px; fill: var(--brand-blue); flex: none; }
  .contact-address { margin-top: 12px; }

  /* Back side */
  .back-lockup {
    position: absolute; inset: 0;
    display: flex; align-items: center; justify-content: center; gap: 18px;
  }
  .brand-mark--back { background: var(--silver); width: 18px; height: 18px; }
  .brand-name--back {
    font-weight: 700; font-size: 40px; letter-spacing: 1px; color: var(--silver);
  }
  .company-stack {
    font-size: 13px; font-weight: 700; line-height: 1.15;
    letter-spacing: 1.5px; color: var(--text-muted);
    border-left: 1px solid var(--divider); padding-left: 14px;
  }
  .company-stack small { font-size: 8px; letter-spacing: 1px; }
</style>
</head>
<body>
<main class="canvas">

  <section class="card card--front" aria-label="Business card front">
    <div class="front-brand">
      <span class="brand-mark"></span>
      <span class="brand-name brand-name--front">VANTRELL</span>
    </div>
    <div class="front-divider"></div>
    <div class="contact">
      <p class="contact-name">Marek Holloway</p>
      <p class="contact-title">Managing Director</p>
      <ul class="contact-list">
        <li><svg viewBox="0 0 10 10"><path d="M2 1h2l1 2-1 1a5 5 0 0 0 2 2l1-1 2 1v2a1 1 0 0 1-1 1A8 8 0 0 1 1 2a1 1 0 0 1 1-1z"/></svg>(044)123456789</li>
        <li><svg viewBox="0 0 10 10"><rect x="2.5" y="0.5" width="5" height="9" rx="1"/></svg>(044)123456789</li>
        <li><svg viewBox="0 0 10 10"><rect x="1" y="3" width="8" height="6"/><rect x="3" y="0.5" width="4" height="2.5"/></svg>(044)123456789</li>
        <li><svg viewBox="0 0 10 10"><path d="M0.5 2h9v6h-9z"/></svg>info@vantrellforge.com</li>
        <li><svg viewBox="0 0 10 10"><circle cx="5" cy="5" r="4.5"/></svg>www.vantrellforge.com</li>
      </ul>
      <p class="contact-address">1234, Address Goes Here,<br>Country name, 12345</p>
    </div>
  </section>

  <section class="card card--back" aria-label="Business card back">
    <div class="back-lockup">
      <span class="brand-mark brand-mark--back"></span>
      <span class="brand-name brand-name--back">VANTRELL</span>
      <p class="company-stack">VANTRELL<br>FORGE<br>WORKS <small>INC</small></p>
    </div>
  </section>

</main>
</body>
</html>
```